PDF flyer for our companies' two main products: Food processing machines.

PDF flyer with showcasing two products. Flyer can be one page per product, or both products on the same page.

Product #1: Labeled "Ribbon blenders".
Showing a photo of the machine, and the details/features offered with that machine. Product description must also say: "Sizes available; 2 Cu Ft. - 450 Cu Ft."

Product #2: Labeled: " Auger hoppers / Screw feeders"
Showing a photo of the machine, and the details/features offered with that machine.

SEE UPLOADED IMAGES; "Ribbon Blenders EXAMPLE FLYER".
& "Auger Hoppers / Screw Conveyors EXAMPLE FLYER" for a rough idea of what we are looking for.

Target Market(s)

Copackers, Packing houses, Food manufacturers, protein powder producers,

Industry/Entity Type

Commercial Food processing / packing / mixing equipment

Font styles to use
Serif

Colors
0054AA
0677BA
7BADD7
CADEEF
E8F1F8

Requirements
Must have
• Company logo on top of flyer.
Nice to have
• I would like for the flyer to show some stock images of common ingredients, similar to the images uploaded.
Should not have
• Pictures with background. Backgrounds must be removed from provides photos. "clipping path"

```html
<!DOCTYPE html>
<html lang="en">
<head>
<meta charset="utf-8">
<title>Steelcore Equipment – Ribbon Blenders &amp; Auger Hoppers</title>
<link rel="stylesheet" href="https://fonts.googleapis.com/css2?family=Montserrat:wght@500;600;700;800&family=Open+Sans:wght@400;600;700&display=swap">
<style>
  :root{
    --blue-deep:#0054AA;
    --blue-mid:#0677BA;
    --blue-soft:#7BADD7;
    --blue-pale:#CADEEF;
    --blue-mist:#E8F1F8;
    --ink:#1b1f2a;
    --white:#ffffff;
    --spice-orange:#e8841c;
    --stage:#eef1f5;
  }
  *{box-sizing:border-box;margin:0;padding:0}
  html,body{width:1200px;height:801px;overflow:hidden;background:var(--stage)}
  body{font-family:"Open Sans",sans-serif;color:var(--ink);position:relative}

  .sheet{position:absolute;top:16px;width:580px;height:769px;background:linear-gradient(160deg,var(--white) 0%,var(--blue-mist) 100%);overflow:hidden;box-shadow:0 2px 10px rgba(0,40,90,.18)}
  .sheet--blender{left:14px}
  .sheet--auger{left:606px}
  .sheet__decor{position:absolute;inset:0;width:580px;height:769px}

  .brand{position:absolute;left:26px;top:34px;display:flex;align-items:center;gap:8px;font-family:"Montserrat",sans-serif;font-weight:800;font-size:22px;letter-spacing:1.5px;color:var(--ink)}
  .brand__dot{width:14px;height:14px;border-radius:50%;background:var(--blue-deep)}

  .hero{position:absolute;border-radius:50%;border:5px solid var(--blue-deep);background:var(--white);display:flex;align-items:center;justify-content:center;overflow:hidden}
  .hero__photo{width:78%;height:62%;border-radius:10px;background:linear-gradient(135deg,#d9dde2 0%,#9aa3ad 55%,#6c737c 100%)}
  .sheet--blender .hero{left:300px;top:20px;width:240px;height:240px}
  .sheet--auger .hero{left:320px;top:14px;width:236px;height:236px}
  .sheet--auger .hero__photo{height:40%}

  .spice{position:absolute;border-radius:50%;box-shadow:0 2px 6px rgba(0,0,0,.25)}
  .spice--mix{background:radial-gradient(circle at 35% 35%,#f0a53a,#b7331d 55%,#4a2a1a)}
  .spice--turmeric{background:radial-gradient(circle at 45% 45%,#f2b230,#dc7a14 60%,#fff 61%)}
  .spice--ginger{background:radial-gradient(circle,#e0b56c 30%,#fff 32%)}
  .spice--seed{background:radial-gradient(circle,#8b7653 30%,#fff 32%)}
  .spice--nut{background:radial-gradient(circle,#5a3a22 30%,#fff 32%)}
  .spice--pod{background:radial-gradient(circle,#9aa25a 30%,#fff 32%)}
  .spice-field{position:absolute;left:420px;top:238px;width:190px;height:190px;border-radius:50%;background:radial-gradient(circle at 45% 45%,#f4c27a 0%,var(--spice-orange) 55%,rgba(232,132,28,0) 72%)}

  .title{position:absolute;font-family:"Montserrat",sans-serif;color:var(--white);text-transform:uppercase}
  .title__main{font-weight:800;font-size:34px;line-height:1.05;letter-spacing:1px}
  .title__sub{margin-top:10px;font-weight:700;font-size:14px;line-height:1.3;letter-spacing:.5px}
  .sheet--blender .title{left:26px;top:214px}
  .sheet--auger .title{left:26px;top:170px}
  .sheet--auger .title__main{font-size:31px}

  .section-bar{position:absolute;height:26px;background:var(--blue-deep);color:var(--white);font-family:"Montserrat",sans-serif;font-weight:700;font-size:12.5px;letter-spacing:.8px;display:flex;align-items:center;padding-left:16px;clip-path:polygon(0 0,100% 0,calc(100% - 14px) 100%,0 100%)}
  .section-bar::after{content:"";position:absolute;right:0;top:0;width:6px;height:100%;background:var(--blue-mid)}

  .feature-list{position:absolute;list-style:none;font-size:10px;line-height:1.4}
  .feature-list li{position:relative;padding-left:16px}
  .feature-list li::before{content:"";position:absolute;left:0;top:2px;width:10px;height:10px;border-radius:50%;background:var(--blue-mid)}
  .feature-list li::after{content:"";position:absolute;left:3px;top:4px;width:4px;height:2px;border-left:1.5px solid var(--white);border-bottom:1.5px solid var(--white);transform:rotate(-45deg)}

  .spec-table{position:absolute;border-collapse:collapse;font-size:7.8px;line-height:1.1}
  .spec-table th,.spec-table td{border:1px solid #2a2f3a;padding:1px 3px;text-align:left;white-space:nowrap}
  .spec-table th{font-weight:700}
  .spec-table thead th{background:var(--blue-pale)}
  .spec-table tbody th{background:var(--blue-mist)}
  .sheet--blender .spec-table{left:24px;top:536px;width:532px}
  .sheet--auger .spec-table{left:24px;top:556px;width:532px;font-size:9px}
  .sheet--auger .spec-table th,.sheet--auger .spec-table td{padding:3px 5px}

  .footer{position:absolute;left:0;bottom:0;width:580px;height:46px;background:var(--blue-deep);color:var(--white);display:flex;align-items:center;gap:18px;padding:0 20px 0 22px;font-size:10.5px}
  .footer::before{content:"";position:absolute;right:0;top:-8px;width:260px;height:8px;background:var(--blue-mid);clip-path:polygon(12px 0,100% 0,100% 100%,0 100%)}
  .footer__item{display:flex;align-items:center;gap:7px}
  .footer__icon{width:22px;height:22px;border:1.5px solid var(--white);border-radius:50%;display:flex;align-items:center;justify-content:center}
  .footer__item--address{margin-left:auto}
</style>
</head>
<body>

<section class="sheet sheet--blender">
  <svg class="sheet__decor" viewBox="0 0 580 769" aria-hidden="true">
    <polygon points="330,0 580,0 580,300 470,300" fill="#0054AA"/>
    <polygon points="0,200 395,200 350,336 0,336" fill="#0054AA"/>
    <polygon points="340,336 395,200 430,200 380,336" fill="#0677BA"/>
    <g stroke="#0054AA" stroke-width="5">
      <line x1="210" y1="22" x2="300" y2="60"/>
      <line x1="210" y1="38" x2="300" y2="76"/>
      <line x1="210" y1="54" x2="300" y2="92"/>
      <line x1="210" y1="70" x2="300" y2="108"/>
    </g>
    <g stroke="#7BADD7" stroke-width="3">
      <line x1="200" y1="86" x2="280" y2="120"/>
    </g>
  </svg>

  <div class="brand"><span class="brand__dot"></span>STEELCORE</div>

  <div class="hero"><div class="hero__photo" role="img" aria-label="Stainless steel ribbon blender on a wheeled frame, background removed"></div></div>

  <div class="spice spice--mix" role="img" aria-label="Bowls of assorted ground spices" style="left:262px;top:226px;width:54px;height:54px"></div>
  <div class="spice spice--mix" role="img" aria-label="Spoons of colourful spices" style="left:326px;top:270px;width:58px;height:58px"></div>

  <div class="title">
    <div class="title__main">Ribbon<br>Blenders</div>
    <div class="title__sub">Sizes available<br>2 Cu Ft. - 450 Cu Ft.</div>
  </div>

  <div class="section-bar" style="left:0;top:344px;width:280px">STANDARD FEATURES</div>
  <ul class="feature-list" style="left:26px;top:378px;width:266px">
    <li>304 stainless steel construction.</li>
    <li>Pre-wired control panels with; batch timer, on/off switch, emergency stop button.</li>
    <li>Food grade compression shaft seals.</li>
    <li>Safety sensor on lid for automatic shutoff when opened.</li>
    <li>Air actuated discharge valve.</li>
    <li>1 piece hinged lid with safety grating.</li>
    <li>Power options; 220v/4.80v.</li>
    <li>24" standard discharge height.</li>
    <li>Castor wheels on 53cf units and smaller</li>
  </ul>

  <div class="section-bar" style="left:298px;top:344px;width:282px">OPTIONS</div>
  <ul class="feature-list" style="left:306px;top:378px;width:262px">
    <li>Dual hinged lids available on custom orders.</li>
    <li>Knife gate style discharge available on custom orders.</li>
    <li>Air purge seals available on custom orders.</li>
    <li>316 stainless material available on custom orders.</li>
    <li>Custom height modification.</li>
    <li>Liquid spray systems</li>
    <li>(VFD) Variable Frequency Drives</li>
    <li>Leg extensions</li>
  </ul>

  <table class="spec-table">
    <thead>
      <tr><th>Model Size</th><th>5cf</th><th>7CF</th><th>10.5CF</th><th>17.5CF</th><th>35CF</th><th>53CF</th><th>70.5CF</th><th>106CF</th></tr>
    </thead>
    <tbody>
      <tr><th>Working Liters</th><td>120L</td><td>200L</td><td>300L</td><td>500L</td><td>1000L</td><td>1500L</td><td>2000L</td><td>3000L</td></tr>
      <tr><th>Fill Capacity</th><td>5CF / 150L</td><td>9CF / 250L</td><td>13CF / 375L</td><td>22CF / 625L</td><td>44CF / 1250L</td><td>66CF / 1875L</td><td>88CF / 2500L</td><td>132CF / 3750L</td></tr>
      <tr><th>Weight</th><td>440lbs</td><td>550lbs</td><td>770lbs</td><td>1212lbs</td><td>1874lbs</td><td>2645lbs</td><td>3527lbs</td><td>5511lbs</td></tr>
      <tr><th>Motor Size</th><td>4hp</td><td>5.3hp</td><td>6.7hp</td><td>10hp</td><td>14.75hp</td><td>20hp</td><td>25hp</td><td>30hp</td></tr>
      <tr><th>Total Length</th><td>50"</td><td>53.5"</td><td>63"</td><td>72"</td><td>94"</td><td>102"</td><td>131.5"</td><td>157.5"</td></tr>
      <tr><th>Total Width</th><td>28"</td><td>34"</td><td>41.5"</td><td>45"</td><td>52"</td><td>66"</td><td>52.5"</td><td>54"</td></tr>
      <tr><th>Total Height</th><td>66"</td><td>69"</td><td>71"</td><td>82"</td><td>87"</td><td>95"</td><td>76"</td><td>110"</td></tr>
      <tr><th>Tub Length</th><td>31.5"</td><td>35.5"</td><td>41"</td><td>47"</td><td>59"</td><td>70"</td><td>75"</td><td>100"</td></tr>
      <tr><th>Tub Width</th><td>16.5"</td><td>22"</td><td>25"</td><td>27.5"</td><td>35.5"</td><td>39"</td><td>48"</td><td>48"</td></tr>
      <tr><th>Tub Height</th><td>20.5"</td><td>26"</td><td>28"</td><td>33"</td><td>41"</td><td>46"</td><td>51"</td><td>53"</td></tr>
      <tr><th>Shaft Diameter</th><td>2"</td><td>2-1/4"</td><td>2-5/8"</td><td>3"</td><td>3.5"</td><td>4"</td><td>4"</td><td>5-1/4"</td></tr>
      <tr><th>Tub Thickness</th><td>3mm</td><td>3mm</td><td>3mm</td><td>4mm</td><td>4mm</td><td>5mm</td><td>5mm</td><td>6mm</td></tr>
      <tr><th>Ribbon Thickness</th><td>6mm</td><td>8mm</td><td>8mm</td><td>8mm</td><td>10mm</td><td>12mm</td><td>12mm</td><td>14mm</td></tr>
      <tr><th>Max RPM</th><td>46 rpm</td><td>46 rpm</td><td>46 rpm</td><td>46 rpm</td><td>30 rpm</td><td>31 rpm</td><td>32 rpm</td><td>33 rpm</td></tr>
    </tbody>
  </table>

  <footer class="footer">
    <span class="footer__item"><span class="footer__icon"><svg width="12" height="9" viewBox="0 0 12 9" fill="none" stroke="#fff" stroke-width="1.2"><rect x=".6" y=".6" width="10.8" height="7.8"/><polyline points=".6,.6 6,5 11.4,.6"/></svg></span>info@steelcore-equip.com</span>
    <span class="footer__item"><span class="footer__icon"><svg width="11" height="11" viewBox="0 0 24 24" fill="#fff"><path d="M6.6 10.8a15.1 15.1 0 0 0 6.6 6.6l2.2-2.2a1 1 0 0 1 1-.25 11.4 11.4 0 0 0 3.6.57 1 1 0 0 1 1 1V20a1 1 0 0 1-1 1A17 17 0 0 1 3 4a1 1 0 0 1 1-1h3.5a1 1 0 0 1 1 1c0 1.25.2 2.45.57 3.57a1 1 0 0 1-.25 1z"/></svg></span>+1 555-010-0199</span>
    <span class="footer__item footer__item--address">1221 Lorem ipsum dolor sit amet consectetur</span>
  </footer>
</section>

<section class="sheet sheet--auger">
  <svg class="sheet__decor" viewBox="0 0 580 769" aria-hidden="true">
    <polygon points="300,0 580,0 580,240 360,240" fill="#0054AA"/>
    <polygon points="0,160 360,160 310,300 0,300" fill="#0054AA"/>
    <polygon points="300,300 360,160 395,160 340,300" fill="#0677BA"/>
    <g stroke="#0054AA" stroke-width="5">
      <line x1="230" y1="70" x2="315" y2="96"/>
      <line x1="230" y1="86" x2="315" y2="112"/>
      <line x1="230" y1="102" x2="315" y2="128"/>
      <line x1="230" y1="118" x2="315" y2="144"/>
    </g>
  </svg>

  <div class="brand"><span class="brand__dot"></span>STEELCORE</div>

  <div class="hero"><div class="hero__photo" role="img" aria-label="Stainless auger hopper with inclined screw feeder tube, background removed"></div></div>

  <div class="spice-field" role="img" aria-label="Scattered turmeric powder"></div>
  <div class="spice spice--turmeric" role="img" aria-label="Mound of turmeric powder" style="left:450px;top:270px;width:100px;height:100px;box-shadow:none"></div>
  <div class="spice spice--ginger" role="img" aria-label="Fresh ginger root" style="left:370px;top:270px;width:56px;height:56px"></div>
  <div class="spice spice--seed" role="img" aria-label="Cumin seeds" style="left:390px;top:334px;width:52px;height:52px"></div>
  <div class="spice spice--nut" role="img" aria-label="Nutmeg" style="left:444px;top:370px;width:50px;height:50px"></div>
  <div class="spice spice--pod" role="img" aria-label="Cardamom pods" style="left:500px;top:380px;width:48px;height:48px"></div>

  <div class="title">
    <div class="title__main">Auger<br>Hoppers /<br>Screw Feeders</div>
  </div>

  <div class="section-bar" style="left:0;top:312px;width:300px">STANDARD FEATURES</div>
  <ul class="feature-list" style="left:26px;top:346px;width:300px">
    <li>Direct Drive.</li>
    <li>304 Stainless steel construction.</li>
    <li>Stainless steel safety grating.</li>
    <li>Pre-wired control panel.</li>
    <li>Electric Vibrator.</li>
    <li>Castor Wheels.</li>
  </ul>

  <div class="section-bar" style="left:0;top:440px;width:340px">OPTIONS</div>
  <ul class="feature-list" style="left:26px;top:474px;width:360px">
    <li>Square or round hopper. 3.5cf and 7cf hoppers are standard.</li>
    <li>Custom hoppers up to 200cf.</li>
    <li>VFD (Variable Frequency Drive).</li>
    <li>Clamshell Auger tube for easy cleanout.</li>
    <li>316 Stainless steel construction.</li>
  </ul>

  <table class="spec-table">
    <thead>
      <tr><th>MODEL</th><th>AH-A2</th><th>AH-A3</th><th>AH-A5</th><th>AH-A7</th><th>AH-A8</th><th>AH-A12</th></tr>
    </thead>
    <tbody>
      <tr><th>FEEDING RATE</th><td>2m³/Hr</td><td>3m³/Hr</td><td>5m³/Hr</td><td>7m³/Hr</td><td>8m³/Hr</td><td>12m³/Hr</td></tr>
      <tr><th>PIPE DIAMETER</th><td>4"</td><td>4-1/2"</td><td>5-1/2"</td><td>6-1/4"</td><td>6-1/2"</td><td>8-1/2"</td></tr>
      <tr><th>HOPPER VOL.</th><td>3.5CF</td><td colspan="5">7CF</td></tr>
      <tr><th>DIMENSIONS</th><td>28.6"x24.4"x31.5"</td><td colspan="5">40" x 32" x 35"</td></tr>
      <tr><th>TOTAL WEIGHT</th><td>221LBS</td><td>287LBS</td><td>397LBS</td><td>441LBS</td><td>485LBS</td><td>596LBS</td></tr>
      <tr><th>CHARGING HEIGHT</th><td colspan="6">STANDARD 72 INCHES. (40" - 196" AVAILABLE)</td></tr>
      <tr><th>CHARGING ANGLE</th><td colspan="6">STANDARD 45° (30° - 60° AVAILABLE)</td></tr>
    </tbody>
  </table>

  <footer class="footer">
    <span class="footer__item"><span class="footer__icon"><svg width="12" height="9" viewBox="0 0 12 9" fill="none" stroke="#fff" stroke-width="1.2"><rect x=".6" y=".6" width="10.8" height="7.8"/><polyline points=".6,.6 6,5 11.4,.6"/></svg></span>info@steelcore-equip.com</span>
    <span class="footer__item"><span class="footer__icon"><svg width="11" height="11" viewBox="0 0 24 24" fill="#fff"><path d="M6.6 10.8a15.1 15.1 0 0 0 6.6 6.6l2.2-2.2a1 1 0 0 1 1-.25 11.4 11.4 0 0 0 3.6.57 1 1 0 0 1 1 1V20a1 1 0 0 1-1 1A17 17 0 0 1 3 4a1 1 0 0 1 1-1h3.5a1 1 0 0 1 1 1c0 1.25.2 2.45.57 3.57a1 1 0 0 1-.25 1z"/></svg></span>+1 555-010-0199</span>
    <span class="footer__item footer__item--address">1221 Lorem ipsum dolor sit amet consectetur</span>
  </footer>
</section>

</body>
</html>
```